Tovel & Associates - London New Letting and Property Management Company *

Tovel & Associates LTD is a new company based in London, and works with brand new residential property in the city centre.

We are aiming to have 1000 new properties a year.

We are looking for something modern and minimalistic :
Logo ,Monogram, Paper Head and Business Card.

Target Market(s)

Internation landlords

Industry/Entity Type

Real Estate

Logo Text

Tovel & Associates

Colors

Designer to choose colors to be used in the design.

Requirements
Nice to have
• A particular monogram with "TA"
Should not have
• Little House over the logo

```html
<!DOCTYPE html>
<html lang="en">
<head>
<meta charset="utf-8">
<title>Tovel &amp; Associates – Letterhead</title>
<link href="https://fonts.googleapis.com/css2?family=Raleway:wght@400;500;600&display=swap" rel="stylesheet">
<style>
  :root {
    --brand: #f39b76;
    --rule: #f3b496;
    --paper: #ffffff;
    --ink: #333333;
    --ink-soft: #555555;
  }
  * { margin: 0; padding: 0; box-sizing: border-box; }
  html, body { width: 1200px; height: 1200px; overflow: hidden; }
  body {
    background: var(--brand);
    font-family: "Raleway", sans-serif;
    color: var(--ink);
    position: relative;
  }
  .sheet {
    position: absolute;
    width: 553px;
    height: 801px;
    background: var(--paper);
    box-shadow: 6px 6px 8px rgba(0,0,0,.35);
    overflow: hidden;
  }
  .sheet--front { left: 27px; top: 23px; }
  .sheet--back { left: 614px; top: 373px; }
  .rule-v, .rule-h { position: absolute; background: var(--rule); }
  .rule-v { width: 1px; top: 0; bottom: 0; }
  .rule-h { height: 1px; left: 0; right: 0; top: 141px; }
  .sheet--front .rule-v { left: 138px; }
  .sheet--back .rule-v { left: 413px; background: var(--brand); }
  .sheet--back .rule-h { background: var(--brand); }

  .brand-name {
    position: absolute;
    color: var(--brand);
    font-weight: 600;
    line-height: 1.05;
  }
  .sheet--front .brand-name { left: 14px; top: 60px; font-size: 17px; }
  .sheet--back .brand-name { left: 32px; top: 590px; font-size: 50px; letter-spacing: .5px; }

  .contact { position: absolute; left: 389px; top: 68px; list-style: none; }
  .contact li {
    display: flex; align-items: center; gap: 8px;
    font-size: 7.6px; color: var(--ink-soft); letter-spacing: .4px;
    height: 17px;
  }
  .icon { width: 12px; height: 12px; flex: none; }

  .date { position: absolute; left: 396px; top: 183px; font-size: 11px; letter-spacing: .5px; }

  .letter { position: absolute; left: 160px; top: 274px; width: 372px; font-size: 11px; line-height: 13.2px; letter-spacing: .35px; }
  .letter p { margin-bottom: 13.2px; }
  .letter .closing { margin: 22px 0 0 2px; }
  .signature { display: block; width: 60px; height: 22px; margin: 22px 0 0 6px; }
  .signer { margin-left: 4px; }
  .signer-name { font-size: 11px; font-weight: 600; color: #111; margin-top: 3px; }
  .signer-role { font-size: 8.5px; color: var(--ink-soft); margin-top: 3px; }

  .web { position: absolute; left: 20px; top: 781px; display: flex; align-items: center; gap: 9px; font-size: 8px; color: var(--ink-soft); letter-spacing: .4px; }
  .band { position: absolute; left: 293px; right: 0; bottom: 0; height: 21px; background: var(--brand); }

  .label { position: absolute; display: flex; align-items: center; gap: 2px; font-size: 5px; color: #5a3324; text-transform: uppercase; }
  .label::before { content: ""; width: 3px; height: 5px; background: var(--paper); }
  .label--back { left: 1110px; top: 327px; }
  .label--front { left: 24px; top: 883px; }
</style>
</head>
<body>

<section class="sheet sheet--front">
  <div class="rule-v"></div>
  <div class="rule-h"></div>

  <div class="brand-name">Tovel &amp;<br>Associates</div>

  <ul class="contact">
    <li>
      <svg class="icon" viewBox="0 0 12 12"><circle cx="6" cy="6" r="6" fill="#f39b76"/><path d="M4 3.3l1 1.3-.6.7a4 4 0 0 0 2.3 2.3l.7-.6 1.3 1-.6 1C5.8 9 3 6.2 3 4z" fill="#fff"/></svg>
      +44 (0) 20 7946 0321
    </li>
    <li>
      <svg class="icon" viewBox="0 0 12 12"><circle cx="6" cy="6" r="6" fill="#f39b76"/><rect x="3.3" y="4" width="5.4" height="4" fill="#fff"/><path d="M3.3 4L6 6.2 8.7 4" stroke="#f39b76" stroke-width=".6" fill="none"/></svg>
      info@tovelassociates.co.uk
    </li>
    <li>
      <svg class="icon" viewBox="0 0 12 12"><circle cx="6" cy="6" r="6" fill="#f39b76"/><path d="M6 2.6a2.3 2.3 0 0 1 2.3 2.3C8.3 6.6 6 9.4 6 9.4S3.7 6.6 3.7 4.9A2.3 2.3 0 0 1 6 2.6z" fill="#fff"/><circle cx="6" cy="4.9" r=".8" fill="#f39b76"/></svg>
      12 Harlow Street, London.
    </li>
  </ul>

  <div class="date">09 November 2018</div>

  <div class="letter">
    <p>Hello Mr Halden,</p>
    <p>I noticed that you have had your home for sale by owner for 4 weeks and was wondering if I could be of any assistance. I recently sold homes in the neighborhood at Ashby Street and have active buyers looking in the area.</p>
    <p>I understand that saving on the commission is probably very important to you. I bet you didn't know that homes that sell with a real estate agent get a higher overall price than those that sold without one — often making up for the difference. I am hoping that we could work together, get the right price on your home and get your home sold.</p>
    <p>Call or text me at +44 (0) 20 7946 0321. We'll set up time, and I'm happy to share my ideas and marketing strategy to get your home sold fast.</p>
    <p class="closing">Best Regards</p>
    <svg class="signature" role="img" aria-label="Handwritten signature of Daniel Orrin" viewBox="0 0 60 22"><rect x="0" y="4" width="60" height="16" fill="#e9e9e9"/></svg>
    <div class="signer">
      <div class="signer-name">Daniel Orrin</div>
      <div class="signer-role">Managing Director, Tovel &amp; Associates LTD</div>
    </div>
  </div>

  <div class="web">
    <svg class="icon" viewBox="0 0 12 12"><circle cx="6" cy="6" r="6" fill="#f39b76"/><circle cx="6" cy="6" r="2.8" fill="none" stroke="#fff" stroke-width=".8"/><path d="M3.2 6h5.6M6 3.2v5.6" stroke="#fff" stroke-width=".6"/></svg>
    tovelassociates.co.uk
  </div>
  <div class="band"></div>
</section>

<div class="label label--back">Letterhead back</div>
<div class="label label--front">Letterhead front</div>

<section class="sheet sheet--back">
  <div class="rule-v"></div>
  <div class="rule-h"></div>
  <div class="brand-name">Tovel &amp;<br>Associates</div>
</section>

</body>
</html>
```